Simple, 1-Page Project - Life-saving AED Devices

We recently kicked off a project to bring all geographic location records for automatic emergency defibrillators (AEDs) in the State of New York online (instead of kept in paper in drawers). This hope is that is will ultimately save thousands of lives, as 9-1-1 operators will be able to quickly direct civilians to the nearest AED to bring to people suffering a cardiac event (e.g., a heart attack).

This page will be used to describe this effort, our progress thus far and how far we have left to go.

I am looking for a 1-page design - coded for both a responsive version for mobile devices and a traditional version - that would ***ideally*** plug into my existing WordPress site (https://qv-lmt.org), but it's not a requirement.

Target Market(s)

General public (non-physicians/non-EMTs)

Requirements
Must have
• - Our logo (please note, our logo is the Birchfield Vale Chapter logo...attached)
Nice to have
• - Would be wonderful to have an area with a clickable map showing where the participating regions are - which, once clicked, will take to you their specific sites. Regions are large chunks of land encompassing multiple towns, NOT a singular, specific place A nice-looking Google Map, a la Plumtail Grids (https://plumtailgrids.com/) would be cool if this were possible..
• - If you need a headline or page title, you can use: "Bringing AEDs in New York Online"
• - Would be nice if the design incorporated the color scheme of our brand (see attachment) and/or our main website: https://qv-lmt.org/
• - Would be nice to have some AED imagery - I attached some common symbols seen in AED advertising for inspiration
Should not have
• - This is a serious topic, so the design should be respectful and not too silly/cartoonish
• - Stock images, if chosen, should be thoughtful and classy

```html
<!DOCTYPE html>
<html lang="en">
<head>
<meta charset="utf-8">
<title>Bringing AEDs in New York Online</title>
<link rel="stylesheet" href="https://fonts.googleapis.com/css2?family=Montserrat:wght@400;500;600;700&family=Lato:wght@400;700&display=swap">
<style>
:root{
  --navy:#0b3470;
  --navy-deep:#082b5e;
  --ink:#1e1e1e;
  --text:#4a4a4a;
  --muted:#6b6b6b;
  --line:#c9c9c9;
  --dark:#1d1c1d;
  --card-dark:#2a2829;
  --footer:#ececec;
  --white:#ffffff;
}
*{box-sizing:border-box;margin:0;padding:0}
html,body{width:1200px;height:3149px;overflow:hidden;background:var(--white)}
body{font-family:"Lato",sans-serif;color:var(--text);position:relative}
.abs{position:absolute}
.btn{position:absolute;display:flex;align-items:center;justify-content:center;font-family:"Montserrat",sans-serif;font-weight:500;letter-spacing:.5px;text-decoration:none}
.btn-navy{background:var(--navy);color:var(--white)}

/* header */
.site-header{position:absolute;top:0;left:0;width:1200px;height:98px;background:var(--white)}
.brand{position:absolute;display:flex;align-items:center;gap:14px}
.brand-mark{width:76px;height:76px;border-radius:50%;background:var(--navy)}
.brand-name{font-family:"Lato",sans-serif;font-weight:700;color:var(--navy);font-size:22px;line-height:23px;letter-spacing:1px;text-transform:uppercase}
.site-header .brand{left:126px;top:10px}
.main-nav{position:absolute;right:112px;top:38px;display:flex;gap:36px}
.main-nav a{font-family:"Montserrat",sans-serif;font-weight:600;font-size:14.5px;color:var(--ink);text-decoration:none;letter-spacing:.4px}

/* hero */
.hero{position:absolute;top:98px;left:0;width:1200px;height:586px;overflow:hidden}
.hero-photo{position:absolute;inset:0;background:linear-gradient(100deg,#6a6a4e 0%,#9a8a6e 22%,#c9b4a0 38%,#5d87b6 55%,#4f7fb3 72%,#2c3038 88%,#22252c 100%)}
.hero-curve{position:absolute;left:0;bottom:0}
.hero-badge{position:absolute;left:111px;top:49px;width:392px;height:392px;border-radius:50%;border:4px solid var(--navy);padding:6px}
.hero-badge-inner{width:100%;height:100%;border-radius:50%;background:rgba(14,60,126,.93);display:flex;flex-direction:column;align-items:center;justify-content:center}
.hero-title{font-family:"Montserrat",sans-serif;font-weight:500;color:var(--white);font-size:29.5px;line-height:35px;text-align:center;letter-spacing:1.2px;margin-top:12px}
.hero-badge .btn{position:static;margin-top:18px;width:168px;height:50px;background:var(--navy-deep);color:var(--white);font-size:16px;border-radius:2px}
.hero-seal{position:absolute;left:553px;top:486px;width:88px;height:88px;border-radius:50%;background:var(--navy);border:5px solid var(--white);box-shadow:0 0 0 2px var(--navy)}

/* about */
.icon-grid{position:absolute;left:107px;top:751px;display:grid;grid-template-columns:repeat(3,149px);grid-auto-rows:144px;column-gap:13px;row-gap:18px}
.icon-tile{border:1px solid var(--line);background:var(--white);display:flex;align-items:center;justify-content:center}
.icon-art{width:88px;height:88px;border-radius:14px;background:linear-gradient(160deg,#e0323a,#b5121b)}
.icon-art.teal{border-radius:50%;background:linear-gradient(160deg,#2a8a96,#16454f)}
.icon-art.dark{background:linear-gradient(160deg,#3a3a3a,#151515)}
.about-copy{position:absolute;left:628px;top:744px;width:470px}
.section-title{font-family:"Montserrat",sans-serif;font-weight:700;color:var(--navy);font-size:33px;letter-spacing:1px}
.about-copy p{font-size:17px;line-height:25px;color:var(--text);margin-top:22px}
.about-copy .btn{position:static;display:flex;margin-top:26px;width:165px;height:50px;font-size:16px}

/* why */
.why{position:absolute;top:1161px;left:0;width:1200px;height:470px}
.why-panel{position:absolute;left:0;top:0;width:598px;height:470px;background:var(--navy)}
.why-panel h2{position:absolute;left:132px;top:100px;font-family:"Montserrat",sans-serif;font-weight:500;color:var(--white);font-size:29px;letter-spacing:.5px}
.why-panel p{position:absolute;left:133px;top:154px;width:410px;font-family:"Montserrat",sans-serif;color:var(--white);font-size:14px;line-height:27px}
.why-panel .btn{left:133px;top:315px;width:170px;height:51px;background:var(--white);color:var(--ink);font-size:16px;border-radius:3px}
.why-photo{position:absolute;left:598px;top:0;width:602px;height:470px;background:radial-gradient(circle at 50% 45%,#d8707e 0%,#a57c9c 28%,#5c8cbd 58%,#476f9b 100%)}

/* regions */
.regions{position:absolute;top:1631px;left:0;width:1200px;height:492px;background:radial-gradient(ellipse at 30% 40%,#2a292a,var(--dark) 70%)}
.region-card{position:absolute;top:75px;width:459px;height:340px;text-decoration:none}
.region-map{height:247px;background:linear-gradient(135deg,#d9dcd8,#bfc4c0 60%,#c7d2c3)}
.region-map.night{background:linear-gradient(135deg,#3b3b3b,#181818 60%,#2d2d2d)}
.region-caption{height:93px;background:var(--card-dark);padding:20px 31px}
.region-caption h3{font-family:"Montserrat",sans-serif;font-weight:500;color:var(--white);font-size:20px;letter-spacing:1px}
.region-caption p{font-family:"Montserrat",sans-serif;color:#e8e8e8;font-size:14.5px;margin-top:8px}

/* blogs */
.blogs-title{position:absolute;left:119px;top:2194px;font-family:"Montserrat",sans-serif;font-weight:500;color:var(--navy);font-size:31px;letter-spacing:.6px}
.blog-card{position:absolute;top:2262px;width:304px;height:378px;background:var(--white);box-shadow:0 2px 8px rgba(0,0,0,.18)}
.blog-photo{height:178px}
.blog-body{padding:26px 24px 0}
.blog-body h3{font-family:"Lato",sans-serif;font-weight:700;color:var(--navy);font-size:18.5px;line-height:20px}
.blog-body p{font-size:13.5px;line-height:18px;color:var(--muted);margin-top:9px}
.blog-body .btn{position:static;display:flex;margin-top:14px;width:122px;height:34px;font-size:13px;font-weight:600}

/* footer */
.site-footer{position:absolute;top:2743px;left:0;width:1200px;height:330px;background:var(--footer)}
.site-footer .brand{left:126px;top:70px}
.footer-col{position:absolute;top:66px}
.footer-col h4{font-family:"Lato",sans-serif;font-weight:700;color:#3a3a3a;font-size:18px;letter-spacing:-.2px}
.contact-line{display:flex;gap:14px;align-items:flex-start;font-size:16px;color:#333;line-height:19px}
.footer-col ul{list-style:none;margin-top:10px}
.footer-col li{font-size:16px;color:#444;line-height:29px;padding-left:4px}
.social li{display:flex;align-items:center;gap:12px;line-height:36px;padding-left:0}
.social-dot{width:26px;height:26px;border-radius:50%;background:var(--navy)}
.copyright{position:absolute;top:3073px;left:0;width:1200px;height:76px;border-top:1px solid #d0d0d0;background:var(--footer);text-align:center;padding-top:28px;font-size:15px;color:#8a8a8a}
</style>
</head>
<body>

<header class="site-header">
  <a class="brand" href="#" style="text-decoration:none">
    <span class="brand-mark"></span>
    <span class="brand-name">Halvern Society<br>of Cardiology</span>
  </a>
  <nav class="main-nav">
    <a href="#">ABOUT US</a><a href="#">SERVICES</a><a href="#">BLOGS</a><a href="#">LOCATION</a><a href="#">NEWS</a><a href="#">CONTACT</a>
  </nav>
</header>

<section class="hero">
  <div class="hero-photo" role="img" aria-label="Bystander performing chest compressions on a person lying on a street"></div>
  <svg class="hero-curve" width="1200" height="80" viewBox="0 0 1200 80">
    <path d="M0 80 L0 64 Q600 -20 1200 64 L1200 80 Z" fill="#ffffff"/>
    <path d="M0 64 Q600 -20 1200 64" fill="none" stroke="#0b3470" stroke-width="3"/>
  </svg>
  <div class="hero-badge">
    <div class="hero-badge-inner">
      <h1 class="hero-title">BRINGING AEDS IN<br>NEW YORK ONLINE</h1>
      <a class="btn" href="#">READ MORE</a>
    </div>
  </div>
  <div class="hero-seal"></div>
</section>

<section class="about">
  <div class="icon-grid">
    <div class="icon-tile"><div class="icon-art" role="img" aria-label="AED sign with heart and lightning bolt"></div></div>
    <div class="icon-tile"><div class="icon-art teal" role="img" aria-label="Round AED heart emblem"></div></div>
    <div class="icon-tile"><div class="icon-art" role="img" aria-label="Red heart with bolt above AED label"></div></div>
    <div class="icon-tile"><div class="icon-art" role="img" aria-label="Red heart with lightning bolt"></div></div>
    <div class="icon-tile"><div class="icon-art dark" role="img" aria-label="Dark heart with yellow bolt and AED label"></div></div>
    <div class="icon-tile"><div class="icon-art dark" role="img" aria-label="Defibrillator device with paddles"></div></div>
  </div>
  <div class="about-copy">
    <h2 class="section-title">ABOUT US</h2>
    <p>Vivamus porttitor purus nisi eleifend libero a tempus libero lectus feugiat felis Morbi diam mauris viverra</p>
    <p>Aravida eu mattis in ante Morbi eget arcu Morbi porta libero id ullamcorper nonummy nibh ligula pulvinar metus eget consectetuer augue nisi quis lacus Ut ac mi quis lacus mollis aliquam Curabitur iaculis tempus eros Curabitur</p>
    <a class="btn btn-navy" href="#">READ MORE</a>
  </div>
</section>

<section class="why">
  <div class="why-panel">
    <h2>WHY WE ARE</h2>
    <p>Vivamus porttitor purus nisi eleifend libero a tempus libero lectus feugiat felis Morbi diam mauris viverra in gravida eu mattis in ante Morbi eget arcu Morbi porta libero id ullamcorper nonummy nibh ligula pulvinar metus eget consectetuer augue nisi quis lacus Ut ac mi</p>
    <a class="btn" href="#">READ MORE</a>
  </div>
  <div class="why-photo" role="img" aria-label="Close view of hands pressing on a chest during CPR"></div>
</section>

<section class="regions">
  <a class="region-card" href="#" style="left:121px">
    <div class="region-map" role="img" aria-label="Light street map of a participating region"></div>
    <div class="region-caption"><h3>CITY TITLE HERE</h3><p>Vivamus porttitor purus nisi eleif</p></div>
  </a>
  <a class="region-card" href="#" style="left:619px">
    <div class="region-map night" role="img" aria-label="Dark street map of a participating region"></div>
    <div class="region-caption"><h3>CITY TITLE HERE</h3><p>Vivamus porttitor purus nisi eleif</p></div>
  </a>
</section>

<h2 class="blogs-title">RECENT BLOGS</h2>
<article class="blog-card" style="left:121px">
  <div class="blog-photo" role="img" aria-label="Older man holding his chest in discomfort" style="background:linear-gradient(135deg,#cfd2d4,#8f9aa6 60%,#b9b2a4)"></div>
  <div class="blog-body">
    <h3>Pellentesque faucibus Ut accumsan ultricies Maecenas</h3>
    <p>Duis quam Nam eget lacus Aliquam erat volutpat Quisque dignissim congue leo Mauris vel lacus vitae felis vestibulum</p>
    <a class="btn btn-navy" href="#">READ MORE</a>
  </div>
</article>
<article class="blog-card" style="left:454px">
  <div class="blog-photo" role="img" aria-label="Hands giving chest compressions" style="background:linear-gradient(135deg,#5b4a3e,#b07f68 40%,#6f9ac6)"></div>
  <div class="blog-body">
    <h3>Pellentesque faucibus Ut accumsan ultricies Maecenas</h3>
    <p>Duis quam Nam eget lacus Aliquam erat volutpat Quisque dignissim congue leo Mauris vel lacus vitae felis vestibulum</p>
    <a class="btn btn-navy" href="#">READ MORE</a>
  </div>
</article>
<article class="blog-card" style="left:787px">
  <div class="blog-photo" role="img" aria-label="Man leaning on a wall clutching his chest" style="background:linear-gradient(135deg,#c9c7c2,#7a5c4c 50%,#e6e4e0)"></div>
  <div class="blog-body">
    <h3>Pellentesque faucibus Ut accumsan ultricies Maecenas</h3>
    <p>Duis quam Nam eget lacus Aliquam erat volutpat Quisque dignissim congue leo Mauris vel lacus vitae felis vestibulum</p>
    <a class="btn btn-navy" href="#">READ MORE</a>
  </div>
</article>

<footer class="site-footer">
  <a class="brand" href="#" style="text-decoration:none">
    <span class="brand-mark"></span>
    <span class="brand-name">Halvern Society<br>of Cardiology</span>
  </a>
  <div class="footer-col" style="left:462px">
    <h4>CONTACT US</h4>
    <div class="contact-line" style="margin-top:18px">
      <svg width="18" height="22" viewBox="0 0 18 22"><path d="M9 1a7 7 0 0 0-7 7c0 5 7 12 7 12s7-7 7-12a7 7 0 0 0-7-7z" fill="none" stroke="#333" stroke-width="1.6"/><circle cx="9" cy="8" r="2.6" fill="none" stroke="#333" stroke-width="1.6"/></svg>
      <span>48 Orrin Lane Suite 6,<br>Dunmore 40711</span>
    </div>
    <div class="contact-line" style="margin-top:20px">
      <svg width="18" height="18" viewBox="0 0 18 18"><path d="M3 1.5l3 .5 1.5 3.5-2 1.5a10 10 0 0 0 5.5 5.5l1.5-2 3.5 1.5.5 3c-1 1-2 1.5-3 1.5C7.5 16.5 1.5 10.5 1.5 4.5c0-1 .5-2 1.5-3z" fill="none" stroke="#333" stroke-width="1.4"/></svg>
      <span>555.014.7720</span>
    </div>
    <div class="contact-line" style="margin-top:20px">
      <svg width="18" height="14" viewBox="0 0 18 14"><rect x="1" y="1" width="16" height="12" fill="none" stroke="#333" stroke-width="1.4"/><path d="M1 1l8 7 8-7" fill="none" stroke="#333" stroke-width="1.4"/></svg>
      <span>hello@halvernsociety.org</span>
    </div>
  </div>
  <div class="footer-col" style="left:712px">
    <h4>COMPANY</h4>
    <ul><li>Home</li><li>About us</li><li>Services</li><li>Blogs</li><li>Contact</li></ul>
  </div>
  <div class="footer-col social" style="left:883px">
    <h4>GET IN TOUCH</h4>
    <ul>
      <li><span class="social-dot"></span>Chirpwire</li>
      <li><span class="social-dot"></span>Friendly Page</li>
      <li><span class="social-dot"></span>Workline</li>
      <li><span class="social-dot"></span>Snapframe</li>
    </ul>
  </div>
</footer>
<div class="copyright">Copyright © 2019 All right reserved</div>

</body>
</html>
```